Harborline Renewal Business Card Design

Professional and clean design. The design colors should flow with the logo. Two-sided card with the website on the back which is:

www.HarborlineRenewal.example.

"Specializing in Water Damage Restoration"

On the front I need the name, email, phone, and logo.

Name: Darnell Quisby
Email: Darnell@HarborlineRenewal.example
Phone: 555-318-2046 for now

I only have the Preview and Thumbnail right now but should have the source files uploaded within a day or two.

Target Market(s)

Flood victims, home owners with water damage from busted pipes etc...

Industry/Entity Type

Business

Contact Information for Business Card

Name: Darnell Quisby

Font styles to use
Serif
Sans Serif

Requirements
Must have
• Business Card Details Info

```html
<!DOCTYPE html>
<html lang="en">
<head>
<meta charset="utf-8">
<title>Harborline Renewal Business Card</title>
<link rel="stylesheet" href="https://fonts.googleapis.com/css2?family=Cinzel:wght@400;600&family=Open+Sans:wght@400;600&display=swap">
<style>
  :root {
    --page: #e9ebed;
    --card: #ffffff;
    --card-shade: #eef0f2;
    --blue: #2fb1de;
    --blue-deep: #1f9bd0;
    --blue-light: #4cc4ea;
    --ink-white: #ffffff;
    --shadow: rgba(20, 40, 60, 0.18);
  }
  * { box-sizing: border-box; margin: 0; padding: 0; }
  html, body {
    width: 1200px; height: 780px; overflow: hidden;
    background: var(--page);
  }
  .sheet {
    position: relative; width: 1200px; height: 780px;
  }
  .card {
    position: absolute; top: 240px;
    width: 520px; height: 300px;
    background: linear-gradient(135deg, var(--card) 0%, var(--card-shade) 100%);
    box-shadow: 0 10px 28px var(--shadow);
    overflow: hidden;
  }
  .card--front { left: 50px; }
  .card--back { left: 630px; }

  /* front */
  .front__band {
    position: absolute; left: 0; top: 0; width: 100%; height: 176px;
    background: radial-gradient(circle at 60% 45%, var(--blue-light) 0%, var(--blue) 55%, var(--blue-deep) 100%);
  }
  .front__name {
    position: absolute; left: 34px; top: 34px;
    font-family: "Cinzel", serif; font-weight: 400;
    font-size: 24px; letter-spacing: 1px;
    color: var(--ink-white);
  }
  .front__contacts {
    position: absolute; left: 34px; top: 92px;
    list-style: none;
    font-family: "Open Sans", sans-serif; font-size: 13px;
    color: var(--ink-white);
  }
  .front__contacts li {
    display: flex; align-items: center; gap: 7px;
    height: 20px;
  }
  .front__contacts .icon { width: 13px; height: 13px; flex: none; }
  .front__web { margin-top: 8px; padding-left: 20px; }

  .front__brand {
    position: absolute; left: 0; top: 176px; width: 100%; height: 124px;
    display: flex; flex-direction: column; align-items: center; justify-content: center;
  }

  /* shared brand block */
  .brand {
    display: flex; align-items: center; gap: 12px;
  }
  .brand__dot {
    width: 38px; height: 38px; border-radius: 50%;
    background: var(--blue);
  }
  .brand__name {
    font-family: "Cinzel", serif; font-weight: 600;
    font-size: 30px; letter-spacing: 1px;
    color: var(--blue);
  }
  .tagline {
    margin-top: 8px;
    font-family: "Open Sans", sans-serif; font-size: 13px;
    color: var(--blue);
  }

  /* back */
  .back__content {
    position: absolute; left: 0; top: 0; width: 100%; height: 240px;
    display: flex; flex-direction: column; align-items: center; justify-content: center;
  }
  .brand--large .brand__dot { width: 46px; height: 46px; }
  .brand--large .brand__name { font-size: 34px; }
  .back__web {
    margin-top: 18px;
    font-family: "Open Sans", sans-serif; font-size: 13px;
    color: var(--blue);
  }
  .back__rule {
    position: absolute; top: 262px; height: 1px; background: var(--blue);
  }
  .back__rule--left { left: 0; width: 170px; }
  .back__rule--right { right: 0; width: 210px; }
</style>
</head>
<body>
<main class="sheet">

  <section class="card card--front" aria-label="Business card front">
    <div class="front__band">
      <h1 class="front__name">DARNELL QUISBY</h1>
      <ul class="front__contacts">
        <li>
          <svg class="icon" viewBox="0 0 13 13" aria-hidden="true">
            <rect width="13" height="13" rx="1.5" fill="#fff"/>
            <path d="M4 3 L5.6 3 L6.2 5 L5.2 5.8 Q6 7.5 7.4 8 L8.2 7 L10 7.6 L10 9.2 Q6.5 10 3.6 5.6 Q3.3 4 4 3 Z" fill="#1f9bd0"/>
          </svg>
          <span>555-318-2046</span>
        </li>
        <li>
          <svg class="icon" viewBox="0 0 13 13" aria-hidden="true">
            <rect width="13" height="13" rx="1.5" fill="#fff"/>
            <rect x="2.5" y="3.8" width="8" height="5.6" fill="none" stroke="#1f9bd0" stroke-width="1"/>
            <path d="M2.5 3.8 L6.5 7 L10.5 3.8" fill="none" stroke="#1f9bd0" stroke-width="1"/>
          </svg>
          <span>Darnell@HarborlineRenewal.example</span>
        </li>
        <li class="front__web">www.HarborlineRenewal.example</li>
      </ul>
    </div>
    <div class="front__brand">
      <div class="brand">
        <span class="brand__dot" aria-hidden="true"></span>
        <span class="brand__name">Harborline Renewal</span>
      </div>
      <p class="tagline">Specializing in Water Damage Restoration</p>
    </div>
  </section>

  <section class="card card--back" aria-label="Business card back">
    <div class="back__content">
      <div class="brand brand--large">
        <span class="brand__dot" aria-hidden="true"></span>
        <span class="brand__name">Harborline Renewal</span>
      </div>
      <p class="tagline">Specializing in Water Damage Restoration</p>
      <p class="back__web">www.HarborlineRenewal.example</p>
    </div>
    <span class="back__rule back__rule--left" aria-hidden="true"></span>
    <span class="back__rule back__rule--right" aria-hidden="true"></span>
  </section>

</main>
</body>
</html>
```